Cleaning Service Company In need of Good Web presence.

The company is a cleaning service company which provides professional staff and service for cleaning. This is a project to build a site that is both solid and a strong recognition of our organization. It is supposed to show quality, cleanliness, professionalism. The use of images and art for imagery is all good just to have a site that is consistent and solid. There might be a chance to make stationary, logo and business cars if someone feels they can build a brand that is consistent. The image we are going for is clean solid and to stand out. Finally stationary should not be expensive to print.

Current logo is attached and can be used or can be made more creative.

Target Market(s)

Corporate and Government entities, that will feel that this company has a brand that sets it apart from the rest. The company is new so the modification of the logo will not be an issue if a more solid brand come out of this project. The idea is to have a clean consistent product that stands our from others in terms of website, stationary, etc

Industry/Entity Type

Cleaning Service

Contact Information for Business Card

P.O.Box 51947
Riffa
Kingdom of Bahrain

Logo Text

Harbor Lane Services

Number of Pages Required

4 page

Font styles to use
Sans Serif

Colors
abd036
cadf82
eaf2ce
9bcb3b

Requirements
Must have
• Green Color to be used in order to stick to the name. Also the creativity and boldness in an elegant manner.
Nice to have
• Arabic name of company
• هاربر لين سرفسس ذ.م.م
• if cannot be put at least make a location should be chosen
• Also could be a bit of 3D given to the logo if it could stay elegent.
Should not have
• Should not show people cleaning.

```html
<!DOCTYPE html>
<html lang="en">
<head>
<meta charset="utf-8">
<title>Harbor Lane Services W.L.L</title>
<link href="https://fonts.googleapis.com/css2?family=Roboto:wght@300;400;500;700;900&family=Roboto+Condensed:wght@400;700&display=swap" rel="stylesheet">
<style>
:root{
  --green:#9bcb3b;
  --lime:#abd036;
  --pale:#cadf82;
  --mist:#eaf2ce;
  --forest:#1f6b34;
  --deep:#0f4d27;
  --ink:#2b2b2b;
  --grey:#6d6d6d;
  --white:#ffffff;
}
*{margin:0;padding:0;box-sizing:border-box}
html,body{width:1200px;height:2496px;overflow:hidden}
body{position:relative;background:var(--white);font-family:"Roboto",Arial,sans-serif;color:var(--ink)}
.abs{position:absolute}

/* top strip + nav */
.top-strip{left:0;top:0;width:1200px;height:18px;background:var(--deep);color:#d9ecb0;font-size:10px;display:flex;justify-content:flex-end;gap:22px;align-items:center;padding-right:40px;z-index:3}
.hero{left:0;top:18px;width:1200px;height:582px;background:linear-gradient(180deg,#8f9a8f 0%,#c9d0cb 35%,#e7ebe7 60%,#9aa39c 100%)}
.nav{left:0;top:18px;width:1200px;height:96px;background:rgba(123,178,40,.85);z-index:2}
.brand{left:40px;top:36px;display:flex;align-items:center;gap:10px;z-index:3}
.brand-dot{width:44px;height:44px;border-radius:50%;background:var(--white)}
.brand-name{color:var(--white);font-weight:700;font-size:15px;line-height:1.2}
.brand-name small{display:block;font-weight:400;font-size:11px}
.menu{right:40px;top:52px;display:flex;gap:0;z-index:3}
.menu a{color:var(--white);text-decoration:none;font-size:12px;padding:8px 22px;border-left:1px solid rgba(255,255,255,.35)}
.menu a.on{background:var(--forest)}
.hero-text{left:0;top:270px;width:1200px;text-align:center;color:var(--white);z-index:2}
.hero-text .kicker{font-size:28px;font-weight:300;letter-spacing:2px}
.hero-text h1{font-family:"Roboto Condensed",sans-serif;font-size:48px;font-weight:700;letter-spacing:1px;margin-top:2px}
.hero-text p{font-size:15px;margin-top:4px}
.btn{display:inline-block;background:var(--green);color:var(--white);font-size:13px;padding:9px 22px;border-radius:3px;text-decoration:none}
.hero-text .btn{margin-top:18px}
.arrow{width:40px;height:40px;border-radius:50%;background:rgba(255,255,255,.55);top:336px;z-index:2}

/* welcome */
.welcome{left:40px;top:650px;width:300px}
.welcome h2{font-size:26px;font-weight:900}
.sub{color:var(--green);font-size:12px;margin-bottom:16px}
.welcome p{font-size:12px;line-height:1.6;color:var(--grey);margin-bottom:12px}
.btn-outline{display:inline-block;border:2px solid var(--green);color:var(--green);font-size:12px;padding:7px 20px;border-radius:3px;margin-top:8px}
.feature{border-radius:50%;color:var(--white);text-align:center;display:flex;flex-direction:column;align-items:center;justify-content:center;padding:24px}
.feature h3{font-size:15px;font-weight:700;margin:6px 0 4px}
.feature p{font-size:10px;line-height:1.4}
.feature b{font-size:11px;margin-top:6px}
.why{left:920px;top:684px;width:240px;height:52px;background:var(--mist);border-left:14px solid var(--green);font-size:22px;font-weight:900;display:flex;align-items:center;justify-content:center;color:var(--forest)}

/* services */
.services{left:0;top:984px;width:1200px;height:570px;background:linear-gradient(180deg,var(--pale),var(--lime))}
.services-title{left:0;top:1030px;width:1200px;text-align:center}
.services-title h2{font-family:"Roboto Condensed",sans-serif;font-size:42px;color:var(--deep);font-weight:700}
.services-title .sub{color:var(--deep)}
.card{top:1196px;width:276px;height:336px;background:var(--forest);color:var(--white)}
.card .photo{height:180px}
.card h3{font-family:"Roboto Condensed",sans-serif;font-size:20px;text-align:center;margin:14px 0 8px}
.card p{font-size:11px;line-height:1.5;padding:0 18px;color:#dcebc2}
.card .btn{margin:12px 0 0 18px;padding:6px 16px;font-size:11px}

/* how it works */
.how{left:40px;top:1594px}
.how h2{font-family:"Roboto Condensed",sans-serif;font-size:36px;font-weight:700}
.how p{font-size:11px;color:var(--grey)}
.step{top:1590px;width:150px;text-align:center}
.step .ring{width:64px;height:64px;border-radius:50%;border:3px solid var(--green);margin:0 auto 10px;display:flex;align-items:center;justify-content:center}
.step span{display:block;font-size:15px;color:var(--forest);line-height:1.25}

/* contact strip */
.strip{left:0;top:1790px;width:1200px;height:100px;border-top:1px solid #ddd;border-bottom:1px solid #ddd;background:#f6f9ee}
.info{top:1812px;display:flex;gap:12px;align-items:flex-start}
.info .dot{width:40px;height:40px;border-radius:50%;background:var(--green);display:flex;align-items:center;justify-content:center;flex:none}
.info h4{font-size:11px;color:var(--green);font-weight:700;margin-bottom:4px}
.info div{font-size:13px;color:var(--ink);line-height:1.4}

/* contact + map */
.contact-bg{left:0;top:1900px;width:600px;height:540px;background:linear-gradient(160deg,#4a4f4b,#2c302d 60%,#3d433e)}
.contact{left:40px;top:1930px;width:360px;color:var(--white)}
.contact h2{font-family:"Roboto Condensed",sans-serif;font-size:32px;font-weight:400;letter-spacing:2px;margin-bottom:30px}
.field{height:40px;border:1px solid rgba(255,255,255,.35);background:rgba(255,255,255,.08);margin-bottom:14px;font-size:12px;padding:12px;color:#cfcfcf}
.field.tall{height:120px}
.map{left:600px;top:1900px;width:600px;height:540px;background:linear-gradient(135deg,#c7dce6,#e9e3d2 55%,#d7cfb8)}

/* footer */
.footer{left:0;top:2440px;width:1200px;height:56px;background:var(--deep);color:#cfe5a8;font-size:11px;display:flex;align-items:center;justify-content:space-between;padding:0 40px}
.social{display:flex;align-items:center;gap:8px}
.social i{width:22px;height:22px;border-radius:50%;background:var(--green);display:block}
</style>
</head>
<body>

<div class="abs top-strip"><span>(000) 555-0142</span><span>info@harborlaneservices.com</span><span>Find us on map</span></div>

<div class="abs hero" role="img" aria-label="Photograph of a bright modern office building interior with glass walls"></div>
<div class="abs nav"></div>
<div class="abs brand">
  <span class="brand-dot"></span>
  <span class="brand-name">Harbor Lane Services<small>هاربر لين سرفسس ذ.م.م</small></span>
</div>
<nav class="abs menu">
  <a class="on">Home</a><a>About Us</a><a>Services</a><a>Process</a><a>Testimonials</a><a>Properties</a><a>Contact Us</a>
</nav>
<div class="abs arrow" style="left:20px"><svg width="40" height="40"><path d="M23 13 L16 20 L23 27" stroke="#444" stroke-width="3" fill="none"/></svg></div>
<div class="abs arrow" style="right:20px"><svg width="40" height="40"><path d="M17 13 L24 20 L17 27" stroke="#444" stroke-width="3" fill="none"/></svg></div>
<div class="abs hero-text">
  <div class="kicker">RELIABLE SERVICE FOR 100%</div>
  <h1>HARBOR LANE SERVICES W.L.L</h1>
  <p>Trusted commercial cleaning for offices, towers and government buildings</p>
  <a class="btn">Call Now</a>
</div>

<section class="abs welcome">
  <h2>WELCOME TO</h2>
  <div class="sub">Harbor Lane Services</div>
  <p>Harbor Lane Services delivers dependable commercial cleaning for offices, towers and public buildings across the kingdom, with trained staff and strict quality checks.</p>
  <p>Every team is supervised, insured and equipped with modern tools, so your spaces stay spotless, safe and ready for work each morning.</p>
  <span class="btn-outline">Details</span>
</section>

<svg class="abs" style="left:600px;top:600px" width="360" height="380" aria-hidden="true">
  <circle cx="128" cy="72" r="100" fill="var(--mist)"/>
  <circle cx="100" cy="260" r="100" fill="var(--mist)"/>
  <circle cx="320" cy="240" r="94" fill="var(--mist)"/>
</svg>
<div class="abs feature" style="left:638px;top:582px;width:180px;height:180px;background:var(--green)">
  <svg width="30" height="30"><circle cx="15" cy="12" r="9" fill="none" stroke="#fff" stroke-width="2"/><path d="M10 19 L8 29 L15 25 L22 29 L20 19" fill="#fff"/></svg>
  <h3>QUALITY</h3><p>Consistent standards and careful checks on every visit.</p><b>Read More</b>
</div>
<div class="abs feature" style="left:610px;top:770;top:770px;width:180px;height:180px;background:var(--forest)">
  <svg width="30" height="30"><path d="M15 3 L18 12 L27 15 L18 18 L15 27 L12 18 L3 15 L12 12 Z" fill="#fff"/></svg>
  <h3>CLEANLINESS</h3><p>Spotless results in every room, floor and surface.</p><b>Read More</b>
</div>
<div class="abs feature" style="left:836px;top:756px;width:168px;height:168px;background:var(--lime)">
  <svg width="30" height="30"><path d="M4 16 L11 10 L19 17 L26 11" stroke="#fff" stroke-width="3" fill="none"/><path d="M4 22 H26" stroke="#fff" stroke-width="3"/></svg>
  <h3>PROFESSIONALISM</h3><p>Trained, uniformed teams who respect your workplace.</p><b>Read More</b>
</div>
<div class="abs why">WHY CHOOSE US?</div>

<div class="abs services"></div>
<div class="abs services-title">
  <h2>Cleaning Services</h2>
  <div class="sub">Harbor Lane Services W.L.L.</div>
</div>
<article class="abs card" style="left:160px">
  <div class="photo" role="img" aria-label="Photo of a tidy office corridor with janitorial supplies" style="background:linear-gradient(160deg,#d8d6c9,#a7a494)"></div>
  <h3>JANITORIAL CLEANING</h3>
  <p>Daily care for lobbies, washrooms and shared areas, with trained janitors on fixed schedules to keep your site fresh.</p>
  <a class="btn">More Info</a>
</article>
<article class="abs card" style="left:462px">
  <div class="photo" role="img" aria-label="Photo of gleaming corporate office windows" style="background:linear-gradient(160deg,#cfe3ef,#8fb2c7)"></div>
  <h3>CORPORATE CLEANING</h3>
  <p>Tailored office cleaning plans for corporate and government clients, handled discreetly before, during or after working hours.</p>
  <a class="btn">More Info</a>
</article>
<article class="abs card" style="left:764px">
  <div class="photo" role="img" aria-label="Photo of a clean building hallway with polished floors" style="background:linear-gradient(160deg,#e2ddd2,#b5a88f)"></div>
  <h3>BUILDINGS CLEANING</h3>
  <p>Full building care from façades and glass to corridors and car parks, planned around your tenants and visitors.</p>
  <a class="btn">More Info</a>
</article>

<section class="abs how">
  <h2>HOW IT WORKS</h2>
  <p>Harbor Lane Services</p>
</section>
<div class="abs step" style="left:440px"><div class="ring"><svg width="30" height="30"><rect x="6" y="4" width="18" height="22" fill="none" stroke="#9bcb3b" stroke-width="2.5"/><path d="M10 11 H20 M10 16 H20 M10 21 H16" stroke="#9bcb3b" stroke-width="2"/></svg></div><span>Submit your<br>service request</span></div>
<div class="abs step" style="left:610px"><div class="ring"><svg width="30" height="30"><path d="M7 16 L13 22 L24 9" stroke="#9bcb3b" stroke-width="3" fill="none"/></svg></div><span>A certified<br>service technician</span></div>
<div class="abs step" style="left:780px"><div class="ring"><svg width="30" height="30"><rect x="5" y="7" width="20" height="18" fill="none" stroke="#9bcb3b" stroke-width="2.5"/><path d="M5 12 H25 M10 4 V9 M20 4 V9" stroke="#9bcb3b" stroke-width="2.5"/></svg></div><span>Reach out<br>to you shortly</span></div>
<div class="abs step" style="left:950px"><div class="ring"><svg width="30" height="30"><circle cx="15" cy="15" r="11" fill="none" stroke="#9bcb3b" stroke-width="2.5"/><path d="M15 8 V15 L20 18" stroke="#9bcb3b" stroke-width="2.5" fill="none"/></svg></div><span>Show Up<br>On Time</span></div>

<div class="abs strip"></div>
<div class="abs info" style="left:160px"><span class="dot"><svg width="20" height="20"><path d="M5 3 L8 3 L10 7 L8 9 Q10 13 12 12 L14 10 L18 12 L18 15 Q10 18 4 9 Z" fill="#fff"/></svg></span><div><h4>MAKE AN APPOINTMENT</h4>(000) 555-0142</div></div>
<div class="abs info" style="left:500px"><span class="dot"><svg width="20" height="20"><rect x="3" y="5" width="14" height="10" fill="none" stroke="#fff" stroke-width="1.8"/><path d="M3 5 L10 11 L17 5" stroke="#fff" stroke-width="1.8" fill="none"/></svg></span><div><h4>EMAIL</h4>info@harborlaneservices.com</div></div>
<div class="abs info" style="left:820px"><span class="dot"><svg width="20" height="20"><path d="M10 18 Q3 10 3 8 A7 7 0 0 1 17 8 Q17 10 10 18 Z" fill="#fff"/><circle cx="10" cy="8" r="2.5" fill="#9bcb3b"/></svg></span><div><h4>VISIT US</h4>P.O.Box 51947, Riffa,<br>Kingdom of Bahrain</div></div>

<div class="abs contact-bg" role="img" aria-label="Dark photo of an office lobby behind the contact form"></div>
<section class="abs contact">
  <h2>CONTACT</h2>
  <div class="field">Name</div>
  <div class="field">Email</div>
  <div class="field">Phone</div>
  <div class="field tall">Message</div>
  <a class="btn">Submit</a>
</section>
<div class="abs map" role="img" aria-label="Map of Bahrain showing the company location"></div>

<footer class="abs footer">
  <span>Copyright © 2017 Harbor Lane Services W.L.L. All rights reserved.</span>
  <span class="social">Connect with us <i></i><i></i><i></i><i></i></span>
</footer>

</body>
</html>
```